Landingpage Design X-Mas Invitation

Every year we invite customers to a special X-Mas Apéro. Since we are an IT-Company we handle the registration process by a landingpage. For this we need a design for the event 2016. The content will be the same as 2015 (you will finde the design attached from last year. There will be an additional job for creating the E-Mail.

Target Market(s)

Customers of IT Company, medium Companys in Central Switzerland

Industry/Entity Type

It Company

Number of Pages Required

1 page

Requirements
Must have
• Christmas Style

```html
<!DOCTYPE html>
<html lang="de">
<head>
<meta charset="utf-8">
<title>Lumena Weihnachtsapéro</title>
<link rel="stylesheet" href="https://fonts.googleapis.com/css2?family=Montserrat:wght@400&family=Roboto:wght@400;500&family=Ubuntu:wght@500&display=swap">
<style>
  :root {
    --accent: #c8452c;
    --white: #ffffff;
    --ink: #222222;
    --footer: #2b2b2b;
    --footer-line: #444444;
    --partner: #5a5a5a;
  }
  * { box-sizing: border-box; margin: 0; padding: 0; }
  html, body { width: 1138px; height: 1200px; overflow: hidden; }
  body { font-family: "Roboto", Arial, sans-serif; background: var(--white); color: var(--ink); position: relative; }

  .site-header { height: 107px; border-top: 3px solid var(--accent); display: flex; justify-content: center; align-items: center; }
  .brand { display: flex; flex-direction: column; align-items: flex-end; line-height: 1; }
  .brand-name { font-family: "Ubuntu", sans-serif; font-weight: 500; font-size: 42px; color: var(--accent); letter-spacing: -0.5px; }
  .brand-sub { font-family: "Ubuntu", sans-serif; font-weight: 500; font-size: 11px; letter-spacing: 1px; color: var(--accent); margin-top: 2px; }

  .hero { position: relative; height: 747px; overflow: hidden; }
  .hero-visual { position: absolute; inset: 0;
    background:
      radial-gradient(ellipse 380px 420px at 230px 330px, rgba(150,95,30,0.85), rgba(70,40,15,0.6) 55%, transparent 80%),
      radial-gradient(ellipse 260px 200px at 120px 140px, rgba(200,140,50,0.6), transparent 75%),
      linear-gradient(90deg, #3a2410 0%, #1c120a 40%, #050505 62%, #000 100%);
  }
  .hero-content { position: absolute; left: 585px; top: 114px; width: 473px; text-align: center; color: var(--white); }
  .hero-title { font-family: "Montserrat", sans-serif; font-weight: 400; font-size: 27px; line-height: 34px; color: var(--accent); margin-bottom: 28px; }
  .hero-text { font-size: 12.5px; line-height: 26.25px; margin-bottom: 26px; }
  .btn-register { display: inline-block; margin-top: 8px; width: 161px; height: 44px; line-height: 44px; border-radius: 22px; background: var(--accent); color: var(--white); font-weight: 500; font-size: 14px; letter-spacing: 0.3px; }

  .partners { height: 129px; display: flex; align-items: center; justify-content: space-between; padding: 0 58px; }
  .partner { display: flex; align-items: center; gap: 5px; font-size: 17px; color: var(--partner); }
  .partner-dot { width: 10px; height: 10px; border-radius: 50%; background: var(--partner); }

  .site-footer { background: var(--footer); height: 217px; color: var(--white); }
  .footer-main { height: 134px; border-bottom: 1px solid var(--footer-line); display: flex; align-items: center; padding: 0 0 0 72px; }
  .footer-brand { display: flex; flex-direction: column; align-items: flex-end; line-height: 1; width: 170px; margin-right: 78px; }
  .footer-brand .brand-name, .footer-brand .brand-sub { color: var(--white); }
  .footer-brand .brand-name { font-size: 40px; }
  .contact-item { display: flex; align-items: center; gap: 14px; }
  .contact-icon { width: 33px; height: 33px; border: 1.5px solid var(--white); border-radius: 50%; display: flex; align-items: center; justify-content: center; flex: none; }
  .contact-text { font-size: 13px; line-height: 21px; }
  .contact-text strong { font-size: 16.5px; font-weight: 500; }
  .item-address { width: 368px; }
  .item-address .contact-text { width: 260px; }
  .item-phone { width: 224px; }
  .copyright { text-align: center; font-size: 13px; padding-top: 34px; }
</style>
</head>
<body>
  <header class="site-header">
    <div class="brand">
      <span class="brand-name">Lumena</span>
      <span class="brand-sub">IT SOLUTIONS</span>
    </div>
  </header>

  <section class="hero">
    <div class="hero-visual" role="img" aria-label="Christbaumkugel mit Schneeflocke vor warmen Lichtern in Bokeh-Unschärfe"></div>
    <div class="hero-content">
      <h1 class="hero-title">Unser traditioneller Lumena Weihnachtsapéro findet</h1>
      <p class="hero-text">am Donnerstag, dem 17.12.2015, zwischen 17 und 20 Uhr in unserer Skylounge an der Tannenweg 18, dem Hauptsitz der Lumena IT Solutions AG statt. In einem aussergewöhnlichen Ambiente können Sie und Ihre Begleitung köstliche Speisen und Getränke beim Apéro Riche geniessen. Desweiteren bietet sich Ihnen die Gelegenheit, ausgiebige Gespräche mit unserer Geschäftsleitung, unseren Mitarbeitenden sowie weiteren Kunden zu führen. Der Anlass findet in einer lockeren Atmosphäre statt, entsprechend ungezwungen ist der Dresscode.</p>
      <p class="hero-text">Ob Sie den ganzen Abend bleiben oder nur kurz nach dem Weihnachts-Shopping vorbeischauen, ist ganz Ihnen überlassen. Wir freuen uns sehr, wenn Sie uns die Gelegenheit geben, Ihnen mit dieser Einladung für die erfolgreiche Zusammenarbeit herzlichst zu danken.</p>
      <span class="btn-register">ANMELDEN</span>
    </div>
  </section>

  <section class="partners" aria-label="Partner">
    <span class="partner"><span class="partner-dot"></span>Brenova</span>
    <span class="partner">Kalvix</span>
    <span class="partner">Tessory</span>
    <span class="partner">Ombrix</span>
    <span class="partner">Vantiro</span>
    <span class="partner">Quellon</span>
    <span class="partner">Dravena</span>
    <span class="partner">Pexora</span>
    <span class="partner">Zurano</span>
    <span class="partner">Malvik</span>
    <span class="partner">Orbenta</span>
  </section>

  <footer class="site-footer">
    <div class="footer-main">
      <div class="brand footer-brand">
        <span class="brand-name">Lumena</span>
        <span class="brand-sub">IT SOLUTIONS</span>
      </div>
      <div class="contact-item item-address">
        <span class="contact-icon">
          <svg width="12" height="16" viewBox="0 0 12 16"><path d="M6 0.5C3 0.5 0.8 2.8 0.8 5.6 0.8 9.5 6 15.5 6 15.5S11.2 9.5 11.2 5.6C11.2 2.8 9 0.5 6 0.5Z" fill="#fff"/><circle cx="6" cy="5.6" r="2" fill="#2b2b2b"/></svg>
        </span>
        <span class="contact-text">KONTAKT :&nbsp;&nbsp; Lumena IT Solutions AG Tannenweg 18 8840 Seebrunn</span>
      </div>
      <div class="contact-item item-phone">
        <span class="contact-icon">
          <svg width="15" height="15" viewBox="0 0 24 24"><path d="M6.6 10.8a15 15 0 0 0 6.6 6.6l2.2-2.2c.3-.3.7-.4 1-.2 1.1.4 2.3.6 3.6.6.6 0 1 .4 1 1V20c0 .6-.4 1-1 1A17 17 0 0 1 3 4c0-.6.4-1 1-1h3.5c.6 0 1 .4 1 1 0 1.3.2 2.5.6 3.6.1.3 0 .7-.2 1z" fill="#fff"/></svg>
        </span>
        <span class="contact-text">Telefon:<br><strong>1800 555 0142</strong></span>
      </div>
      <div class="contact-item">
        <span class="contact-icon">
          <svg width="16" height="12" viewBox="0 0 16 12"><rect x="1" y="1" width="14" height="10" rx="1.5" fill="none" stroke="#fff" stroke-width="1.5"/><path d="M1.5 2 8 7l6.5-5" fill="none" stroke="#fff" stroke-width="1.5"/></svg>
        </span>
        <span class="contact-text">Email:<br>info@lumena.example</span>
      </div>
    </div>
    <p class="copyright">Copyright ©, Lumena.&nbsp; All Rights Reserved.</p>
  </footer>
</body>
</html>
```